GearHive.com

Our company, GearHive Inc., is an established business with an extensive worldwide customer base in the Aviation, Aerospace, and Defense Industries.
GearHive Inc, is an e-commerce platform driven by an aviation parts locator. We are looking to totally redo our homepage, log-in page, standard part search page, and results page.
Our current web design is in 800frame and we need it to be updated to a centered 1280 frame. The new design also needs to be easily viewed from any mobile device. The new size needs to accommodate 2-3 advertisements, both vertically and horizontally.
I like clean, simple, crisp lines that can easily be navigated by everyone. Along with Aviation/Aerospace stock photos, I would like to use different shades of blue and grey and accent specific buttons/drop-downs with orange or yellow.
We are also looking for a web designer who also has the ability to cut up the page and turn over to our .NET developers.
Attached are the 4 pages that I would like to start working on. The standard content within these pages need to be incorporated into the new design.
Our current website is www.gearhive.com
Below are some industry websites that I like the color and feel of.
Please use attached pic of corvane T410 as main photo
http://www.stravelcorp.com/
http://www.quillanor.com/en/aerospace.html
http://www.dexavend.com/
http://aerospace.veltrimax.com/

```html
<!DOCTYPE html>
<html lang="en">
<head>
<meta charset="utf-8">
<title>GearHive.com – Aviation Parts Locator</title>
<link href="https://fonts.googleapis.com/css2?family=Open+Sans:wght@400;600;700;800&display=swap" rel="stylesheet">
<style>
:root{
  --navy:#0f2457;
  --blue:#1d57b8;
  --blue-bright:#2f7fd8;
  --blue-light:#4a9be6;
  --sky:#9fc6ec;
  --grey-bg:#eceef1;
  --grey-line:#cfd4da;
  --grey-text:#6b7380;
  --ink:#2a3140;
  --orange:#f28a1a;
  --footer:#1e2532;
  --footer-deep:#151a24;
  --white:#ffffff;
}
*{box-sizing:border-box;margin:0;padding:0}
html,body{width:781px;height:1200px;overflow:hidden}
body{background:var(--grey-bg);font-family:"Open Sans",Arial,sans-serif;color:var(--ink);position:relative}
a{color:inherit;text-decoration:none}

/* top navigation */
.topnav{height:20px;background:var(--navy);display:flex;justify-content:center;gap:2px}
.topnav a{font-size:7px;color:#c9d6ef;padding:0 10px;line-height:20px}
.topnav a.active{background:var(--blue-bright);color:var(--white)}

/* brand header */
.brandbar{height:63px;background:linear-gradient(90deg,#f2f6fb 0%,#e3ecf8 30%,#2a5fb5 55%,#123a86 100%);display:flex;align-items:center;justify-content:space-between;padding:0 46px}
.brand{display:flex;align-items:center;gap:7px;font-size:24px;font-weight:800;color:var(--blue)}
.brand .mark{width:16px;height:16px;background:var(--orange)}
.quicklinks{display:flex;gap:26px}
.quicklinks a{font-size:7.5px;color:var(--white);font-weight:600;letter-spacing:.3px}
.quicklinks b{color:var(--orange)}

.tagline{height:16px;background:var(--blue-bright);display:flex;align-items:center;justify-content:space-between;padding:0 46px 0 46px}
.tagline p{font-size:6.5px;color:var(--white)}
.btn-login{background:var(--orange);color:var(--white);font-size:6.5px;font-weight:700;padding:0 14px;height:16px;line-height:16px}

/* hero */
.hero{position:relative;height:286px;background:linear-gradient(180deg,#2d5f9e 0%,#6f9ed0 45%,#b9d3ec 75%,#8e9aa6 100%)}
.hero-copy{position:absolute;left:46px;top:26px;width:360px;color:var(--white)}
.hero-copy h1{font-size:17px;font-weight:700;line-height:1.2}
.hero-copy p{font-size:7px;margin-top:8px;line-height:1.45;color:#e6eefa}
.hero-actions{display:flex;gap:8px;margin-top:12px}
.btn{font-size:6.5px;font-weight:700;color:var(--white);padding:0 14px;height:18px;line-height:18px}
.btn-blue{background:var(--blue-bright)}
.btn-orange{background:var(--orange)}
.hero-arrow{position:absolute;top:134px;width:18px;height:18px;border-radius:50%;background:rgba(255,255,255,.35)}
.hero-arrow.left{left:4px}.hero-arrow.right{right:4px}
.dots{display:flex;gap:5px;justify-content:center}
.dots span{width:5px;height:5px;border-radius:50%;background:rgba(255,255,255,.55)}
.dots span.on{background:var(--white)}
.hero .dots{position:absolute;bottom:10px;left:0;right:0}

/* features */
.features{position:relative;display:flex;justify-content:center;gap:0;padding:22px 40px 0;height:230px}
.features .rail{position:absolute;left:80px;right:80px;top:54px;height:1px;background:var(--grey-line)}
.feature{width:175px;text-align:center;position:relative}
.feature .circle{width:62px;height:62px;border-radius:50%;background:var(--white);border:2px solid var(--grey-line);margin:0 auto;display:flex;align-items:center;justify-content:center}
.feature.active .circle{background:var(--blue-bright);border-color:var(--blue-bright)}
.feature h3{font-size:8px;font-weight:700;margin-top:14px;letter-spacing:.3px}
.feature.active h3{color:var(--blue-bright)}
.feature p{font-size:6px;color:var(--grey-text);line-height:1.5;margin:5px 22px 0}
.readmore{display:inline-block;font-size:6.5px;font-weight:700;color:var(--blue-bright);margin-top:8px}

/* news & events */
.updates{padding:0 44px;height:258px}
.updates-head{display:flex;border-bottom:1px solid var(--grey-line);padding-bottom:4px}
.updates-head div{width:347px;display:flex;justify-content:space-between;align-items:flex-end}
.updates-head div + div{margin-left:0;padding-left:0}
.updates-head h2{font-size:9px;font-weight:700}
.updates-head a{font-size:5.5px;color:var(--blue-bright);margin-right:10px}
.cards{display:flex;gap:5px;margin-top:10px}
.card{width:170px}
.card .photo{height:118px}
.card .body{background:var(--blue-bright);color:var(--white);height:68px;padding:8px 9px}
.card .body p{font-size:6.5px;font-weight:600;line-height:1.45}
.card .body a{display:block;font-size:5.5px;margin-top:6px;color:#dbe8fa}

/* testimonial */
.testimonial{position:relative;height:92px;background:linear-gradient(180deg,#2d6fcf 0%,#1c4fa4 100%);text-align:center;color:var(--white);padding-top:22px}
.testimonial blockquote{font-size:10px;line-height:1.3}
.testimonial cite{display:block;font-style:normal;font-size:7px;font-weight:700;margin-top:8px;letter-spacing:.4px}
.testimonial .dots{margin-top:10px}

/* footer */
.footer{background:linear-gradient(180deg,#2a3447 0%,var(--footer) 100%);height:130px;padding:18px 46px 0;display:flex;gap:0}
.fcol{width:172px}
.fcol h4{font-size:7.5px;font-weight:700;color:var(--white);letter-spacing:.3px;margin-bottom:5px}
.fcol .sub{display:flex;gap:16px}
.fcol ul{list-style:none}
.fcol li{font-size:5.5px;color:#a9b3c4;line-height:1.75}
.fcol li.lead{color:var(--white);font-weight:600}
.social{display:flex;gap:4px;margin-top:6px}
.social span{width:11px;height:11px;border-radius:50%;background:var(--blue-bright)}
.bottombar{height:42px;background:var(--footer-deep);display:flex;justify-content:space-between;align-items:center;padding:0 46px}
.bottombar nav{display:flex;gap:16px}
.bottombar nav a{font-size:6px;color:#c1c9d6}
.bottombar p{font-size:5.5px;color:#8791a2;margin-top:3px}
.bottombar .clock{font-size:6px;color:#c1c9d6}
</style>
</head>
<body>

<nav class="topnav">
  <a class="active" href="#">Home</a><a href="#">About</a><a href="#">Membership</a><a href="#">Buyers</a><a href="#">Suppliers</a><a href="#">Government Data</a><a href="#">Advertise</a><a href="#">Media</a><a href="#">FAQ's</a><a href="#">Contact</a>
</nav>

<header class="brandbar">
  <div class="brand"><span class="mark"></span>GearHive</div>
  <div class="quicklinks">
    <a href="#">GEARHIVE <b>MAIN</b></a>
    <a href="#">WHITE <b>PAGES</b></a>
    <a href="#">MESSAGE <b>BOARD</b></a>
  </div>
</header>

<div class="tagline">
  <p>The Gateway to the Aviation, Aerospace and Defense Industries</p>
  <a class="btn-login" href="#">LOGIN</a>
</div>

<section class="hero" role="img" aria-label="Business jet parked nose-on on the tarmac under a blue sky">
  <div class="hero-copy">
    <h1>Government Bidding? Detailed Logistics &amp; Notification</h1>
    <p>Updated Solicitation Information. Receive a mail notification when a Government Solicitation matches your inventory !</p>
    <div class="hero-actions">
      <a class="btn btn-blue" href="#">LEARN MORE</a>
      <a class="btn btn-orange" href="#">FREE TRIAL SIGN UP NOW</a>
    </div>
  </div>
  <span class="hero-arrow left"></span><span class="hero-arrow right"></span>
  <div class="dots"><span class="on"></span><span></span><span></span><span></span></div>
</section>

<section class="features">
  <div class="rail"></div>
  <div class="feature">
    <div class="circle"><svg width="26" height="26" viewBox="0 0 26 26" fill="none" stroke="#1d57b8" stroke-width="2"><circle cx="13" cy="13" r="10"/><path d="M8 13l3 3 7-7"/></svg></div>
    <h3>SOLUTIONS</h3>
    <p>Find trusted parts sources fast with tools built for buyers, sellers and repair shops worldwide.</p>
    <a class="readmore" href="#">READ MORE</a>
  </div>
  <div class="feature">
    <div class="circle"><svg width="26" height="26" viewBox="0 0 26 26" fill="none" stroke="#1d57b8" stroke-width="2"><circle cx="9" cy="9" r="4"/><circle cx="18" cy="9" r="4"/><path d="M2 22c1-5 13-5 14 0M11 22c1-5 13-5 14 0"/></svg></div>
    <h3>OUR COMMUNITY</h3>
    <p>Join thousands of aviation members who share data, leads and answers every single day.</p>
    <a class="readmore" href="#">READ MORE</a>
  </div>
  <div class="feature active">
    <div class="circle"><svg width="26" height="26" viewBox="0 0 26 26" fill="none" stroke="#ffffff" stroke-width="2"><circle cx="13" cy="13" r="10"/><path d="M3 13h20M13 3c4 4 4 16 0 20M13 3c-4 4-4 16 0 20"/></svg></div>
    <h3>INDUSTRY CONNECTIONS</h3>
    <p>Connect with suppliers, agencies and partners across the global aerospace supply chain.</p>
    <a class="readmore" href="#">READ MORE</a>
  </div>
  <div class="feature">
    <div class="circle"><svg width="26" height="26" viewBox="0 0 26 26" fill="none" stroke="#1d57b8" stroke-width="2"><path d="M13 3l3 6 7 1-5 5 1 7-6-3-6 3 1-7-5-5 7-1z"/></svg></div>
    <h3>MEMBER ADVANTAGES</h3>
    <p>Members get priority listings, alerts and reports that help close deals in less time.</p>
    <a class="readmore" href="#">READ MORE</a>
  </div>
</section>

<section class="updates">
  <div class="updates-head">
    <div><h2>LATEST NEWS</h2><a href="#">VIEW ALL NEWS</a></div>
    <div><h2>EVENTS</h2><a href="#">VIEW ALL EVENTS</a></div>
  </div>
  <div class="cards">
    <article class="card">
      <div class="photo" role="img" aria-label="Jet engine close-up" style="background:linear-gradient(160deg,#5b7fa8,#2c4870)"></div>
      <div class="body"><p>New engine parts program opens this month for all verified supplier members.</p><a href="#">READ MORE</a></div>
    </article>
    <article class="card">
      <div class="photo" role="img" aria-label="Radar display screen" style="background:linear-gradient(160deg,#2f4b63,#0f1e2d)"></div>
      <div class="body"><p>Defense tracking data now added to the search results for every member account.</p><a href="#">READ MORE</a></div>
    </article>
    <article class="card">
      <div class="photo" role="img" aria-label="Airliner climbing into a cloudy sky" style="background:linear-gradient(180deg,#8fb6de,#dfe9f3)"></div>
      <div class="body"><p>Meet our team at the spring airshow and learn about the new parts locator.</p><a href="#">READ MORE</a></div>
    </article>
    <article class="card">
      <div class="photo" role="img" aria-label="Aircraft hangar with jets at dusk" style="background:linear-gradient(180deg,#b6c9dc,#6c8299)"></div>
      <div class="body"><p>Register now for the annual aerospace expo and trade day in the fall.</p><a href="#">READ MORE</a></div>
    </article>
  </div>
</section>

<section class="testimonial">
  <blockquote>We had an AOG issue last night. I logged into GearHive.com and had the part ordered in about five minutes.</blockquote>
  <cite>DAN MORROW, HALCREST INDUSTRIES, INC.</cite>
  <div class="dots"><span class="on"></span><span></span><span></span><span></span></div>
</section>

<footer class="footer">
  <div class="fcol" style="width:200px">
    <h4>SOLUTIONS</h4>
    <div class="sub">
      <ul><li class="lead">Buyer Solutions</li><li>Parts Search</li><li>International Sourcing</li><li>Quote Requests</li><li>Request for Quotes</li><li>Quality Assurance</li></ul>
      <ul><li class="lead">Supplier Solutions</li><li>List Parts</li><li>Government Bids</li><li class="lead">Government Data</li><li>NSN Search</li><li>Bid Alerts</li></ul>
    </div>
  </div>
  <div class="fcol" style="width:190px">
    <h4>OUR COMMUNITY</h4>
    <div class="sub">
      <ul><li>Commercial Aviation</li><li>General Aviation</li><li>Military / Defense</li><li>Aerospace</li><li>Helicopters</li><li>Repair Stations</li></ul>
      <ul><li>Distributors</li><li>Manufacturers</li><li>Government Agencies</li><li>Brokers</li></ul>
    </div>
  </div>
  <div class="fcol" style="width:150px">
    <h4>INDUSTRY CONNECTIONS</h4>
    <ul><li>Trade Directory</li><li>Show Calendar</li><li>Associations</li><li>Partner Network</li><li>Market Reports</li><li>Advertise With Us</li></ul>
    <div class="social"><span></span><span></span><span></span><span></span><span></span></div>
  </div>
</footer>

<div class="bottombar">
  <div>
    <nav><a href="#">Home</a><a href="#">About Us</a><a href="#">Employment</a><a href="#">Contact Us</a><a href="#">Privacy</a><a href="#">Policy Sitemap</a></nav>
    <p>Copyright@2015 GearHive Inc. All Rights Reserved.</p>
  </div>
  <span class="clock">EST</span>
</div>

</body>
</html>
```